Business Card Design

We have recently seen two business cards that caught our attention and think the designs would work for us. We are an accounting firm that serves small businesses in a variety of industries. Attached are the two business card that inspired us along with very rough layouts. We would like to see a professional layout using our company information.

Industry/Entity Type

Accounting

Contact Information for Business Card

Company Name - Marlowe Thistle
Address - 4182 Orlanby Lane, Suite 610, Houston, TX 77093
713-555-0187 - Main
281-555-0342 - Fax

Team Member Names, emails and phone numbers (see attachment)

```html
<!DOCTYPE html>
<html lang="en">
<head>
<meta charset="utf-8">
<title>Marlowe Thistle – Business Card</title>
<link rel="stylesheet" href="https://fonts.googleapis.com/css2?family=Libre+Baskerville:wght@700&family=Open+Sans:wght@300;400;600;700&display=swap">
<style>
  :root {
    --bg: #8a8a8a;
    --card-light: #fbfbfb;
    --card-mid: #dcdcdc;
    --ink: #2b2b2b;
    --ink-soft: #555555;
    --block: #3a3a3a;
    --tab: #b9b9b9;
  }
  * { box-sizing: border-box; margin: 0; padding: 0; }
  html, body { width: 1200px; height: 894px; overflow: hidden; }
  body {
    background: var(--bg);
    font-family: "Open Sans", Arial, sans-serif;
    color: var(--ink);
    position: relative;
  }
  .card {
    position: absolute;
    left: 250px;
    width: 700px;
    height: 400px;
    background: radial-gradient(ellipse at 45% 40%, var(--card-light) 0%, #efefef 45%, var(--card-mid) 100%);
    box-shadow: 0 6px 18px rgba(0,0,0,.25);
    overflow: hidden;
  }
  .card--front { top: 30px; }
  .card--back { top: 464px; }

  .brand {
    position: absolute;
    display: flex;
    align-items: center;
    gap: 14px;
  }
  .brand__mark {
    width: 38px; height: 38px;
    background: var(--ink);
  }
  .brand__name {
    font-family: "Libre Baskerville", Georgia, serif;
    font-weight: 700;
    font-size: 36px;
    color: var(--ink);
    letter-spacing: .5px;
  }
  .card--front .brand { left: 250px; top: 78px; }
  .card--back .brand { left: 50%; top: 110px; transform: translateX(-50%); }

  .person { position: absolute; left: 0; top: 150px; display: flex; align-items: flex-start; }
  .person__block { width: 38px; height: 74px; background: var(--block); }
  .person__text { margin-left: 20px; padding-top: 12px; }
  .person__name { font-size: 30px; font-weight: 700; letter-spacing: 1px; line-height: 1; }
  .person__title { font-size: 14px; font-weight: 300; letter-spacing: 6.5px; margin-top: 6px; color: var(--ink-soft); }

  .contact {
    position: absolute; left: 420px; top: 258px;
    list-style: none;
    font-size: 14px; font-weight: 600;
    color: var(--ink);
  }
  .contact__item { display: flex; align-items: flex-start; gap: 12px; margin-bottom: 10px; line-height: 1.3; }
  .contact__icon { width: 16px; height: 16px; flex: none; margin-top: 1px; fill: var(--ink-soft); }

  .socials {
    position: absolute; left: 0; right: 0; bottom: 70px;
    display: flex; justify-content: space-around;
    list-style: none; padding: 0 60px;
  }
  .social { display: flex; align-items: center; gap: 10px; font-size: 15px; color: var(--ink-soft); }
  .social__box { width: 18px; height: 18px; background: var(--ink); }

  .card__tab { position: absolute; right: 0; top: 150px; width: 14px; height: 74px; background: var(--tab); }
</style>
</head>
<body>

  <section class="card card--front" aria-label="Business card front">
    <div class="brand">
      <span class="brand__mark"></span>
      <span class="brand__name">Marlowe Thistle</span>
    </div>

    <div class="person">
      <span class="person__block"></span>
      <div class="person__text">
        <p class="person__name">DANA WHITCOMBE</p>
        <p class="person__title">GENERAL MANAGER</p>
      </div>
    </div>

    <ul class="contact">
      <li class="contact__item">
        <svg class="contact__icon" viewBox="0 0 16 16"><path d="M8 1 1 7.5h2V15h4v-4h2v4h4V7.5h2z"/></svg>
        <span>4182 Orlanby Lane, Suite 610<br>Houston, TX 77093</span>
      </li>
      <li class="contact__item">
        <svg class="contact__icon" viewBox="0 0 16 16"><circle cx="8" cy="8" r="6.5" fill="none" stroke="#555" stroke-width="1.4"/><path d="M1.5 8h13M8 1.5c-3 3.5-3 9.5 0 13M8 1.5c3 3.5 3 9.5 0 13" fill="none" stroke="#555" stroke-width="1.2"/></svg>
        <span>www.marlowethistle.com</span>
      </li>
      <li class="contact__item">
        <svg class="contact__icon" viewBox="0 0 16 16"><path d="M1 3h14v10H1z"/><path d="M1 3l7 6 7-6" fill="none" stroke="#eee" stroke-width="1.2"/></svg>
        <span>dana@marlowethistle.com</span>
      </li>
      <li class="contact__item">
        <svg class="contact__icon" viewBox="0 0 16 16"><path d="M4 1h2l1.2 3.5-1.6 1.2a9 9 0 0 0 4.7 4.7l1.2-1.6L15 10v2a2 2 0 0 1-2 2C6.5 14 2 9.5 2 3a2 2 0 0 1 2-2z"/></svg>
        <span>713-555-0187 &nbsp;·&nbsp; Fax 281-555-0342</span>
      </li>
    </ul>
  </section>

  <section class="card card--back" aria-label="Business card back">
    <div class="brand">
      <span class="brand__mark"></span>
      <span class="brand__name">Marlowe Thistle</span>
    </div>

    <ul class="socials">
      <li class="social"><span class="social__box"></span>yourname</li>
      <li class="social"><span class="social__box"></span>@yourname</li>
      <li class="social"><span class="social__box"></span>yourname</li>
    </ul>

    <span class="card__tab"></span>
  </section>

</body>
</html>
```